Website for IT consulting Company

I need a website upgrade, the existing site content is ok, I would also like to add a testimonial page, the site should be something that is easy for us to update content. You use the content from www.kelvanbrook.com as an example. I will also post update logo and artwork. I also need a contact form with some type of validation or captcha.

I added Coded to the Project

Please omit Address maps

Target Market(s)

small business, service oriented companies. We provide IT Consulting, support and mangement

Industry/Entity Type

Information Technology

Coding

Number of Pages Required

1 page

Font styles to use
Serif
Sans Serif

Requirements
Must have
• Contain logo attached, and content from existing web site www.kelvanbrook.com.
• Also need to update content easily, and be movable to different platforms.
• There is a catch phrase
• "Let us worry about your technology…” “ so you don’t have to!”
• Should be included.
Nice to have
• Testimonial page, Project page where we can post new and past projects and pictures
Should not have
• none

```html
<!DOCTYPE html>
<html lang="en">
<head>
<meta charset="utf-8">
<title>Kelvanbrook Development Group, Inc – IT Consulting</title>
<link rel="stylesheet" href="https://fonts.googleapis.com/css2?family=Exo+2:ital,wght@0,600;0,700;0,800;1,700;1,800&family=Arimo:wght@400;700&family=Tinos&display=swap">
<style>
:root{
  --black:#000;
  --blue:#1a8fd6;
  --blue-dark:#0f6fb0;
  --blue-light:#35a9ea;
  --ink:#1c1c1c;
  --grey-bg:#e8e8e8;
  --grey-mid:#9a9a9a;
  --grey-panel:#8e8f91;
  --white:#fff;
  --head:'Exo 2',sans-serif;
  --body:'Arimo',sans-serif;
  --serif:'Tinos',serif;
}
*{box-sizing:border-box;margin:0;padding:0}
html,body{width:1200px;height:2557px;overflow:hidden;background:var(--white)}
body{font-family:var(--body);color:var(--ink);position:relative}
section,header,nav,footer{position:absolute;left:0;width:1200px}
.abs{position:absolute}

/* header */
.site-header{top:0;height:124px;background:var(--black)}
.brand{left:82px;top:36px;display:flex;align-items:center;gap:14px}
.brand-mark{width:58px;height:58px;background:var(--blue);border-radius:8px}
.brand-name{font-family:var(--head);font-weight:800;font-size:42px;color:var(--white);letter-spacing:1px}
.follow{left:850px;top:18px;display:flex;align-items:center;gap:10px;color:var(--white);font-family:var(--head);font-style:italic;font-weight:700;font-size:18px}
.social{display:flex;gap:8px}
.social span{width:26px;height:26px;background:#8c8c8c;display:block}
.contact-chip{top:68px;display:flex;align-items:center;gap:12px;color:var(--white);font-family:var(--head);font-weight:700;font-size:21px}
.chip-icon{width:40px;height:40px;background:var(--blue);border-radius:4px;display:flex;align-items:center;justify-content:center}

/* nav */
.main-nav{top:124px;height:57px;background:linear-gradient(#3aa8e8,#1383cc)}
.main-nav a{position:absolute;top:17px;transform:translateX(-50%);font-family:var(--head);font-style:italic;font-weight:700;font-size:19px;color:var(--white);text-decoration:none;letter-spacing:.5px;white-space:nowrap}
.main-nav a.active{color:#1a3550}

/* hero */
.hero{top:181px;height:532px;background:linear-gradient(180deg,#3f4449 0%,#4d5257 45%,#2f3a2f 78%,#1c2419 100%)}
.hero-mark{left:560px;top:155px;width:80px;height:80px;background:var(--blue);border-radius:12px}
.hero-line1{left:0;top:270px;width:100%;text-align:center;font-family:var(--head);font-style:italic;font-weight:800;font-size:32px;color:var(--white)}
.hero-line2{left:0;top:320px;width:100%;text-align:center;font-family:var(--head);font-style:italic;font-weight:800;font-size:32px;color:var(--blue-light)}
.dots{top:482px;left:567px;display:flex;gap:5px}
.dots span{width:9px;height:9px;background:#777}
.dots span.on{background:var(--white)}

/* welcome */
.welcome{top:713px;height:265px;text-align:center}
.section-title{font-family:var(--head);font-style:italic;font-weight:800;color:var(--ink);letter-spacing:.5px}
.section-title em{font-style:inherit;color:var(--blue)}
.welcome .section-title{position:absolute;left:0;top:42px;width:100%;font-size:26px}
.rule{position:absolute;left:560px;width:80px;height:3px;background:var(--blue)}
.welcome p{position:absolute;left:85px;width:1030px;top:107px;font-size:14px;line-height:26px;color:#222}
.read-more-link{position:absolute;left:0;top:200px;display:block;width:100%;text-align:center;font-family:var(--head);font-style:italic;font-weight:800;font-size:15px;color:var(--blue-dark);text-decoration:underline}

/* services */
.services{top:978px;height:577px;background:var(--grey-bg)}
.services .section-title{position:absolute;left:0;top:46px;width:100%;text-align:center;font-size:30px}
.services svg{position:absolute;left:0;top:0}
.svc-label{font-family:'Exo 2',sans-serif;font-style:italic;font-weight:800;font-size:16px;fill:#1c1c1c}
.svc-brand{font-family:'Exo 2',sans-serif;font-weight:800;font-size:40px;fill:#8a8a8a}

/* panels */
.panels{top:1555px;height:385px}
.panel{position:absolute;top:0;height:385px}
.panel-support{left:0;width:605px;background:linear-gradient(180deg,#2aa0e6,#1277bf)}
.panel-outsource{left:605px;width:595px;background:linear-gradient(180deg,#c9c9ca,#77787a)}
.notch{position:absolute;left:578px;top:0;width:0;height:0;border-left:27px solid transparent;border-right:27px solid transparent;border-top:30px solid var(--grey-bg)}
.panel h3{position:absolute;top:60px;font-family:var(--head);font-style:italic;font-weight:800;font-size:24px;display:flex;align-items:center;gap:12px;white-space:nowrap}
.panel-support h3{left:85px;color:var(--white)}
.panel-outsource h3{left:31px;color:var(--ink)}
.panel-line{position:absolute;top:110px;height:1px}
.photo{position:absolute;top:130px;width:205px;height:184px;border:2px solid rgba(255,255,255,.6)}
.panel-support .photo{left:85px;background:linear-gradient(135deg,#1e3c5c,#5a7fa3 60%,#c7d5e3)}
.panel-outsource .photo{left:31px;background:linear-gradient(135deg,#0c2440,#2b6fb0 55%,#9fd0f2)}
.panel p{position:absolute;top:124px;width:275px;font-size:14px;line-height:26px}
.panel-support p{left:310px;color:var(--white)}
.panel-outsource p{left:254px;color:var(--white)}
.btn-more{position:absolute;top:275px;width:152px;height:38px;display:flex;align-items:center;justify-content:center;gap:10px;font-family:var(--serif);font-size:17px;color:var(--white)}
.panel-support .btn-more{left:310px;background:linear-gradient(#a9a9a9,#7b7b7b)}
.panel-outsource .btn-more{left:254px;background:linear-gradient(#39aaea,#1580c8)}

/* cta */
.cta{top:1940px;height:245px;text-align:center}
.cta h2{position:absolute;left:0;top:42px;width:100%;font-family:var(--head);font-style:italic;font-weight:800;font-size:35px;color:var(--ink)}
.cta h4{position:absolute;left:0;top:90px;width:100%;font-family:var(--head);font-style:italic;font-weight:800;font-size:29px;color:var(--ink)}
.call-btn{position:absolute;left:472px;top:151px;width:190px;height:49px;background:linear-gradient(#9c9c9c,#6d6d6d);border-radius:6px;display:flex;align-items:center;gap:8px;padding-left:10px;color:var(--white);font-family:var(--head);font-style:italic;font-weight:800;text-align:left;line-height:19px}
.call-btn small{font-size:16px;display:block}
.call-btn b{font-size:19px}
.call-mark{position:absolute;left:665px;top:143px;width:62px;height:62px;background:var(--blue);border-radius:10px}

/* footer */
.site-footer{top:2185px;height:328px;background:linear-gradient(180deg,#2d2f31 0%,#3b3a38 50%,#2a2520 100%)}
.foot-title{position:absolute;top:62px;font-family:var(--head);font-style:italic;font-weight:800;font-size:18px;color:var(--white)}
.foot-title em{font-style:inherit;color:var(--blue-light)}
.quick-links{position:absolute;left:85px;top:96px;list-style:none}
.quick-links li{font-size:14px;color:var(--white);height:25px;display:flex;align-items:center;gap:12px}
.quick-links li::before{content:"";width:4px;height:4px;border-radius:50%;background:var(--blue-light)}
.contact-block{position:absolute;left:286px;top:97px;color:var(--white);font-size:14px;line-height:21px}
.contact-row{display:flex;align-items:center;gap:16px;margin-top:10px}
.inquiry{position:absolute;left:598px;top:104px;width:225px}
.field{background:var(--white);border:1px solid #ccc;height:33px;margin-bottom:4px;font-size:12px;color:#333;padding:4px 6px}
.field.msg{height:58px}
.submit{width:92px;height:28px;background:var(--blue);border:1px solid #8fd0f5;color:var(--white);font-family:var(--head);font-weight:800;font-style:italic;font-size:14px;display:flex;align-items:center;justify-content:center;margin-top:8px}
.foot-mark{position:absolute;left:900px;top:70px;display:flex;flex-direction:column;align-items:center;gap:14px}
.foot-mark span{width:150px;height:150px;background:var(--blue);border-radius:18px;display:block}
.foot-mark b{font-family:var(--head);font-weight:800;font-size:26px;color:var(--blue-light)}

.bottom-bar{left:0;top:2513px;width:1200px;height:44px;background:linear-gradient(#2aa0e6,#1377c0)}
.copyright{left:85px;top:14px;font-family:var(--head);font-style:italic;font-weight:700;font-size:14px;color:var(--white)}
.bottom-bar .follow{left:856px;top:8px}
</style>
</head>
<body>

<header class="site-header">
  <div class="abs brand"><span class="brand-mark"></span><span class="brand-name">KELVANBROOK</span></div>
  <div class="abs follow">Follow Us On
    <div class="social"><span></span><span></span><span></span><span></span></div>
  </div>
  <div class="abs contact-chip" style="left:757px">
    <span class="chip-icon"><svg width="22" height="22" viewBox="0 0 24 24"><path d="M6.6 10.8c1.4 2.8 3.8 5.1 6.6 6.6l2.2-2.2c.3-.3.7-.4 1-.2 1.1.4 2.3.6 3.6.6.6 0 1 .4 1 1V20c0 .6-.4 1-1 1C10.6 21 3 13.4 3 4c0-.6.4-1 1-1h3.5c.6 0 1 .4 1 1 0 1.3.2 2.5.6 3.6.1.3 0 .7-.2 1z" fill="#fff"/></svg></span>
    (555) 014-2290
  </div>
  <div class="abs contact-chip" style="left:980px">
    <span class="chip-icon"><svg width="24" height="24" viewBox="0 0 24 24"><circle cx="12" cy="8" r="4.5" fill="#fff"/><path d="M3 22c0-5 4-8 9-8s9 3 9 8z" fill="#fff"/></svg></span>
    SUPPORT
  </div>
</header>

<nav class="main-nav">
  <a class="active" style="left:123px">HOME</a>
  <a style="left:264px">ABOUT US</a>
  <a style="left:423px">SERVICES</a>
  <a style="left:581px">PROJECTS</a>
  <a style="left:733px">CLIENTS</a>
  <a style="left:881px">CAREERS</a>
  <a style="left:1050px">CONTACT US</a>
</nav>

<section class="hero" role="img" aria-label="City skyline photograph at dusk with downtown towers above a tree line">
  <span class="abs hero-mark"></span>
  <div class="abs hero-line1">Let Us Worry About Your Technology...</div>
  <div class="abs hero-line2">So You Don’t Have To!</div>
  <div class="abs dots"><span></span><span></span><span></span><span class="on"></span></div>
</section>

<section class="welcome">
  <h1 class="section-title">WELCOME TO KELVANBROOK <em>DEVELOPMENT GROUP, INC</em></h1>
  <span class="rule" style="top:83px"></span>
  <p>Kelvanbrook Development Group, Inc. was established in 1991. Our mission is helping businesses and individuals realize a Return on Investment by implementing today’s advanced technologies. As a small business we understand the importance of technology and personalized attention.&nbsp; Every member of our support team has worked with both large and small companies supporting a multitude of applications, networks and environments.</p>
  <a class="read-more-link">READ MORE</a>
</section>

<section class="services">
  <h2 class="section-title">OUR <em>SERVICES</em></h2>
  <svg width="1200" height="577" viewBox="0 0 1200 577">
    <defs>
      <linearGradient id="iconFill" x1="0" y1="0" x2="0" y2="1">
        <stop offset="0" stop-color="#3aaeee"/><stop offset="1" stop-color="#0f74bd"/>
      </linearGradient>
    </defs>
    <path d="M372 577 A228 228 0 0 1 828 577 Z" fill="#fff"/>
    <path d="M372 577 A228 228 0 0 1 828 577" fill="none" stroke="#9a9a9a" stroke-width="9"/>
    <g stroke="#8a8a8a" stroke-width="2" stroke-dasharray="3 4" fill="none">
      <line x1="380" y1="508" x2="273" y2="484"/>
      <line x1="408" y1="432" x2="314" y2="363"/>
      <line x1="461" y1="366" x2="394" y2="285"/>
      <line x1="533" y1="322" x2="498" y2="224"/>
      <line x1="610" y1="300" x2="617" y2="195"/>
      <line x1="697" y1="318" x2="733" y2="225"/>
      <line x1="770" y1="360" x2="835" y2="285"/>
      <line x1="820" y1="432" x2="917" y2="374"/>
      <line x1="826" y1="508" x2="958" y2="484"/>
    </g>
    <g fill="#fff" stroke="#8a8a8a" stroke-width="3">
      <circle cx="380" cy="508" r="8"/><circle cx="408" cy="432" r="8"/><circle cx="461" cy="366" r="8"/>
      <circle cx="533" cy="322" r="8"/><circle cx="610" cy="300" r="8"/><circle cx="697" cy="318" r="8"/>
      <circle cx="770" cy="360" r="8"/><circle cx="820" cy="432" r="8"/><circle cx="826" cy="508" r="8"/>
    </g>
    <g fill="url(#iconFill)" stroke="#fff" stroke-width="3">
      <circle cx="273" cy="484" r="48"/><circle cx="314" cy="363" r="48"/><circle cx="394" cy="285" r="48"/>
      <circle cx="498" cy="224" r="48"/><circle cx="617" cy="195" r="48"/><circle cx="733" cy="225" r="48"/>
      <circle cx="835" cy="285" r="48"/><circle cx="917" cy="374" r="48"/><circle cx="958" cy="484" r="48"/>
    </g>
    <g fill="none" stroke="#fff" stroke-width="3" stroke-linecap="round">
      <rect x="253" y="470" width="40" height="26" rx="2"/><line x1="263" y1="503" x2="283" y2="503"/>
      <circle cx="306" cy="352" r="9"/><path d="M290 384c0-12 8-17 16-17s16 5 16 17"/><rect x="318" y="360" width="16" height="12"/>
      <line x1="394" y1="278" x2="394" y2="308"/><circle cx="394" cy="274" r="4"/><path d="M383 264a15 15 0 0 0 0 20M405 264a15 15 0 0 1 0 20"/>
      <line x1="491" y1="212" x2="491" y2="236"/><line x1="505" y1="212" x2="505" y2="236"/>
      <rect x="599" y="178" width="36" height="11" rx="3"/><rect x="599" y="192" width="36" height="11" rx="3"/><circle cx="628" cy="211" r="6"/>
      <rect x="713" y="210" width="32" height="22" rx="2"/><rect x="742" y="220" width="12" height="18" rx="2"/>
      <path d="M820 300l22-22 8 8-22 22zM846 276l8-8"/>
      <path d="M901 378a22 22 0 0 1 32 0M908 385a12 12 0 0 1 18 0"/><rect x="900" y="390" width="34" height="8" rx="2"/>
      <path d="M958 462l18 7v14c0 12-8 18-18 22-10-4-18-10-18-22v-14z"/>
    </g>
    <text class="svc-label" x="163" y="490" text-anchor="middle">DESKTOP</text>
    <text class="svc-label" x="163" y="508" text-anchor="middle">SUPPORT</text>
    <text class="svc-label" x="195" y="369" text-anchor="middle">NETWORK</text>
    <text class="svc-label" x="195" y="387" text-anchor="middle">ADMINISTRATION</text>
    <text class="svc-label" x="225" y="274" text-anchor="middle">TELECOMMUNICATIONS</text>
    <text class="svc-label" x="335" y="199" text-anchor="middle">AUDIO/VIDEO MULTIMEDIA</text>
    <text class="svc-label" x="620" y="141" text-anchor="middle">DISASTER RECOVERY</text>
    <text class="svc-label" x="782" y="190">WEB DESIGN</text>
    <text class="svc-label" x="899" y="275">NETWORK CABLING</text>
    <text class="svc-label" x="981" y="366">WIRELESS</text>
    <text class="svc-label" x="981" y="384">NETWORKS</text>
    <text class="svc-label" x="1016" y="475">ANTIVIRUS</text>
    <text class="svc-label" x="1016" y="493">SOLUTIONS</text>
    <rect x="564" y="388" width="72" height="72" rx="10" fill="#1a8fd6"/>
    <text class="svc-brand" x="600" y="520" text-anchor="middle">KELVANBROOK</text>
  </svg>
</section>

<section class="panels">
  <div class="panel panel-support">
    <h3><svg width="32" height="34" viewBox="0 0 32 34"><circle cx="16" cy="9" r="7" fill="#fff"/><path d="M3 33c0-9 6-13 13-13s13 4 13 13z" fill="#fff"/><rect x="2" y="29" width="28" height="4" fill="#fff"/></svg>IT SUPPORT SOLUTIONS</h3>
    <span class="panel-line" style="left:85px;width:488px;background:rgba(255,255,255,.4)"></span>
    <div class="photo" role="img" aria-label="Two technicians working beside server racks in a data centre"></div>
    <p>Lorem ipsum dolor sit amet, consecretk etuer adipiscing elit, sed diam nonumre my nibh euismod tinciduntol ut laoret et re olore magna aliquam erat volutpt. Ut wisi minim consequat.</p>
    <a class="btn-more">Read More <span>⟶</span></a>
  </div>
  <div class="panel panel-outsource">
    <h3><svg width="36" height="34" viewBox="0 0 36 34"><circle cx="18" cy="8" r="6" fill="#1c1c1c"/><path d="M8 24c0-7 4-10 10-10s10 3 10 10z" fill="#1c1c1c"/><rect x="2" y="24" width="32" height="3" fill="#1c1c1c"/><path d="M6 27v7M30 27v7M3 4v14M33 4v14" stroke="#1c1c1c" stroke-width="2.5"/></svg>WHY OUTSOURCE TECHNOLOGIES</h3>
    <span class="panel-line" style="left:31px;width:530px;background:rgba(255,255,255,.5)"></span>
    <div class="photo" role="img" aria-label="Hand holding a tablet with a glowing globe and floating screens"></div>
    <p>Lorem ipsum dolor sit amet, consecretk etuer adipiscing elit, sed diam nonumre my nibh euismod tinciduntol ut laoret et re olore magna aliquam erat volutpt. Ut wisi minim consequat.</p>
    <a class="btn-more">Read More <span>⟶</span></a>
  </div>
  <span class="notch"></span>
</section>

<section class="cta">
  <h2>IT Solutions That Works For Your Business</h2>
  <h4>A Full Service Technology Company</h4>
  <div class="call-btn">
    <svg width="30" height="30" viewBox="0 0 24 24"><path d="M6.6 10.8c1.4 2.8 3.8 5.1 6.6 6.6l2.2-2.2c.3-.3.7-.4 1-.2 1.1.4 2.3.6 3.6.6.6 0 1 .4 1 1V20c0 .6-.4 1-1 1C10.6 21 3 13.4 3 4c0-.6.4-1 1-1h3.5c.6 0 1 .4 1 1 0 1.3.2 2.5.6 3.6.1.3 0 .7-.2 1z" fill="#fff"/></svg>
    <div><small>Call Us Today</small><b>(555) 014-2290</b></div>
  </div>
  <span class="call-mark"></span>
</section>

<footer class="site-footer" role="img" aria-label="Night city skyline photograph behind the footer">
  <h5 class="foot-title" style="left:85px">Quick <em>Links</em></h5>
  <ul class="quick-links">
    <li>Home</li><li>About Us</li><li>Services</li><li>Projects</li><li>Clients</li><li>Careers</li><li>Contact Us</li>
  </ul>
  <h5 class="foot-title" style="left:286px">Contact <em>Details</em></h5>
  <div class="contact-block">
    <div>Kelvanbrook Development Group, Inc.</div>
    <div style="margin-top:18px">418 Marlow Ave.<br>Riverton, Texas 77090</div>
    <div class="contact-row" style="margin-top:16px"><svg width="14" height="14" viewBox="0 0 24 24"><path d="M6.6 10.8c1.4 2.8 3.8 5.1 6.6 6.6l2.2-2.2c.3-.3.7-.4 1-.2 1.1.4 2.3.6 3.6.6.6 0 1 .4 1 1V20c0 .6-.4 1-1 1C10.6 21 3 13.4 3 4c0-.6.4-1 1-1h3.5c.6 0 1 .4 1 1 0 1.3.2 2.5.6 3.6.1.3 0 .7-.2 1z" fill="#35a9ea"/></svg>(555) 014-2290</div>
    <div class="contact-row"><svg width="14" height="14" viewBox="0 0 24 24"><rect x="6" y="2" width="12" height="6" fill="#35a9ea"/><rect x="2" y="8" width="20" height="10" rx="2" fill="#35a9ea"/><rect x="6" y="14" width="12" height="8" fill="#fff"/></svg>(555) 014-2290</div>
    <div class="contact-row"><svg width="14" height="12" viewBox="0 0 24 18"><rect width="24" height="18" fill="#35a9ea"/><path d="M0 0l12 10L24 0" fill="none" stroke="#fff" stroke-width="2"/></svg>info@kelvanbrook.com</div>
  </div>
  <h5 class="foot-title" style="left:598px">Quick <em>Inquiry</em></h5>
  <div class="inquiry">
    <div class="field">Name</div>
    <div class="field">Email</div>
    <div class="field msg">Message</div>
    <div class="submit">SUBMIT</div>
  </div>
  <div class="foot-mark"><span></span><b>KELVANBROOK</b></div>
</footer>

<div class="abs bottom-bar">
  <div class="abs copyright">Copyright © 2017 Kelvanbrook Development Group, Inc. All Rights Reserved.</div>
  <div class="abs follow">Follow Us On
    <div class="social"><span></span><span></span><span></span><span></span></div>
  </div>
</div>

</body>
</html>
```